4th Generation Family Business Needs a New Card Design!

We are a family owned 4th Generation company. We are based in the Sydney, Australia area and we are desperately in need of a more modern and classy card. We are monumental masons who design, supply & erect lasting memorials throughout cemeteries in Sydney. Our customers are normally in a period of grieving. I have attached logo files that will need to be implemented on the card. Company was established 1935. Australian Owned and Operated. Card needs to be designed to PIXO.com specification.

Target Market(s)

Our target market is based upon people that a grieving for family members that have passed away. We also deal with alot of companies that own and operate cemeteries.

Industry/Entity Type

Business

Contact Information for Business Card

Simon Harcourt, Operations Manager, 0417293086, simon@harcourtmemorials.com.au
Lewis Harcourt, Director, 0491630572, lewis@harcourtmemorials.com.au
Phone # 02 9561 3048
Website: www.harcourtmemorials.com.au
Address: Suite 17, 8 Palfrey Lane, West Carlow, Sydney NSW 2156

Font styles to use
Serif
Decorative
Script

Requirements
Must have
• Would like to see the logo nicely implemented with a modern design. Embossed lettering would be a nice additive.

```html
<!DOCTYPE html>
<html lang="en">
<head>
<meta charset="utf-8">
<title>Harcourt Memorials – Business Card</title>
<link rel="stylesheet" href="https://fonts.googleapis.com/css2?family=Source+Sans+3:wght@400;600&display=swap">
<style>
  :root {
    --backdrop: #3a332f;
    --card: #151515;
    --card-edge: #232323;
    --gold: #e9b824;
    --white: #f2f2f2;
    --muted: #d6d6d6;
    --rule: #5a5a5a;
  }
  * { box-sizing: border-box; margin: 0; padding: 0; }
  html, body {
    width: 1200px; height: 844px; overflow: hidden;
    background: var(--backdrop);
    font-family: "Source Sans 3", "Myriad Pro", sans-serif;
  }
  .canvas {
    position: relative; width: 1200px; height: 844px;
    display: flex; align-items: center; justify-content: center; gap: 60px;
  }
  .card {
    position: relative; width: 520px; height: 316px;
    background: var(--card);
    border: 1px solid var(--card-edge);
    box-shadow: 0 10px 28px rgba(0,0,0,.45);
  }
  /* contact side */
  .card--contact { display: flex; }
  .brand-panel {
    width: 245px; display: flex; flex-direction: column;
    align-items: center; justify-content: center; padding: 0 18px;
  }
  .wordmark {
    display: flex; flex-direction: column; align-items: center;
    color: var(--white); font-weight: 600; text-align: center; line-height: 1.05;
  }
  .wordmark__square { width: 14px; height: 14px; background: var(--white); margin-bottom: 12px; }
  .wordmark__name { font-size: 36px; letter-spacing: 1px; }
  .wordmark__sub { font-size: 22px; letter-spacing: 3px; }
  .address {
    margin-top: 30px; color: var(--muted); font-size: 15px;
    line-height: 1.3; text-align: center;
  }
  .divider { width: 1px; background: var(--rule); margin: 22px 0; }
  .contact-panel { flex: 1; padding: 34px 0 0 20px; color: var(--white); }
  .person { margin-bottom: 20px; }
  .person__name { color: var(--gold); font-weight: 600; font-size: 17px; line-height: 1.15; }
  .person__role { font-size: 14px; line-height: 1.25; }
  .line { display: flex; align-items: center; gap: 6px; font-size: 13.5px; line-height: 1.3; }
  .line svg { width: 10px; height: 10px; flex: none; fill: var(--gold); }
  .office { margin-top: 18px; }
  .office .line { font-size: 14px; line-height: 1.45; }
  /* logo side */
  .card--brand { display: flex; align-items: center; justify-content: center; }
  .card--brand .wordmark__name { font-size: 50px; }
  .card--brand .wordmark__sub { font-size: 30px; }
  .card--brand .wordmark__square { width: 18px; height: 18px; margin-bottom: 18px; }
</style>
</head>
<body>
<main class="canvas">
  <section class="card card--contact" aria-label="Contact side">
    <div class="brand-panel">
      <div class="wordmark">
        <span class="wordmark__square"></span>
        <span class="wordmark__name">Harcourt</span>
        <span class="wordmark__sub">Memorials</span>
      </div>
      <p class="address">Suite 17, 8 Palfrey Lane, West Carlow,<br>Sydney NSW 2156</p>
    </div>
    <div class="divider"></div>
    <div class="contact-panel">
      <div class="person">
        <p class="person__name">Simon Harcourt</p>
        <p class="person__role">Operations Manager</p>
        <p class="line"><svg viewBox="0 0 10 10"><rect x="2.5" y="0" width="5" height="10" rx="1"/></svg>0417293086</p>
        <p class="line"><svg viewBox="0 0 10 10"><path d="M0 2h10v6H0z M0 2l5 3.5L10 2" /></svg>simon@harcourtmemorials.com.au</p>
      </div>
      <div class="person">
        <p class="person__name">Lewis Harcourt</p>
        <p class="person__role">Director</p>
        <p class="line"><svg viewBox="0 0 10 10"><rect x="2.5" y="0" width="5" height="10" rx="1"/></svg>0491630572</p>
        <p class="line"><svg viewBox="0 0 10 10"><path d="M0 2h10v6H0z M0 2l5 3.5L10 2" /></svg>lewis@harcourtmemorials.com.au</p>
      </div>
      <div class="office">
        <p class="line"><svg viewBox="0 0 10 10"><path d="M1 3c0-2 8-2 8 0v1H7V3H3v1H1z M2 5h6l1 4H1z"/></svg>02 9561 3048</p>
        <p class="line"><svg viewBox="0 0 10 10"><circle cx="5" cy="5" r="5"/></svg>www.harcourtmemorials.com.au</p>
      </div>
    </div>
  </section>

  <section class="card card--brand" aria-label="Brand side">
    <div class="wordmark">
      <span class="wordmark__square"></span>
      <span class="wordmark__name">Harcourt</span>
      <span class="wordmark__sub">Memorials</span>
    </div>
  </section>
</main>
</body>
</html>
```